Halverstone Minerals Web Design

Require a Web page design for an international mining and private investment company currently based in Dubai, UAE. I would like to view designs that incorporate our current corporate logo design aimed at communicating global business development/expansion across a diversity of commodities within the mining and investment sectors.

We are a global organisation with global experience and strategy with specific business development focus in Africa, Central and South America.

Target Market(s)

Mining industry, finance, fund raising, brokering, private equity and public stock exchanges.

Industry/Entity Type

Mining

Number of Pages Required

5+ page

Font styles to use
Sans Serif

Colors

Designer to choose colors to be used in the design.

Requirements
Must have
• Corporate logo, description of who we are, what we do, corporate mission, vision & strategy.
Nice to have
• Inclusion of images, photos, interactive maps/graphics and video.

```html
<!DOCTYPE html>
<html lang="en">
<head>
<meta charset="utf-8">
<title>Halverstone Minerals</title>
<link rel="stylesheet" href="https://fonts.googleapis.com/css2?family=Montserrat:wght@400;600;700&family=Open+Sans:wght@400;600&display=swap">
<style>
:root{
  --gold:#b8994f;
  --gold-dark:#9c7f3a;
  --gold-light:#d4bb7c;
  --ink:#2a2a2a;
  --charcoal:#262524;
  --text:#555;
  --muted:#888;
  --paper:#fff;
  --grey:#efefef;
  --band:#f4f2ee;
}
*{box-sizing:border-box;margin:0;padding:0}
html,body{width:1200px;height:2632px;overflow:hidden}
body{font-family:"Open Sans",Arial,sans-serif;color:var(--text);background:var(--paper)}
h1,h2,h3,.nav a,.btn,.brand{font-family:"Montserrat",Arial,sans-serif}

.top{height:104px;display:flex;align-items:center;justify-content:space-between;padding:0 84px}
.brand{display:flex;align-items:center;gap:12px;color:var(--gold);font-weight:700;font-size:24px;letter-spacing:.5px}
.brand .mark{width:22px;height:22px;background:var(--gold)}
.call{display:flex;align-items:center;gap:12px;font-family:"Montserrat",sans-serif;font-size:14px;font-weight:600;color:var(--ink)}
.call .ico{width:40px;height:40px;border-radius:50%;background:var(--gold);display:flex;align-items:center;justify-content:center}

.nav{height:40px;background:var(--gold);display:flex;justify-content:center;gap:0}
.nav a{color:#fff;text-decoration:none;font-size:12px;font-weight:600;text-transform:uppercase;line-height:40px;padding:0 44px}

.hero{position:relative;height:416px;background:radial-gradient(ellipse at 50% 30%,#6a5638 0%,#3a2f22 45%,#161310 100%);text-align:center;color:#fff}
.hero h1{position:absolute;top:196px;left:0;right:0;font-size:34px;color:var(--gold-light);letter-spacing:1px}
.hero p{position:absolute;top:246px;left:320px;right:320px;font-size:13px;font-weight:600;line-height:22px;text-transform:uppercase}
.hero .btn{position:absolute;top:352px;left:50%;transform:translateX(-50%)}
.arrow{position:absolute;top:196px;width:34px;height:34px;border-radius:50%;background:rgba(255,255,255,.85);display:flex;align-items:center;justify-content:center}
.arrow.left{left:24px}.arrow.right{right:24px}

.btn{display:inline-block;background:var(--gold);color:#fff;font-size:11px;font-weight:700;text-transform:uppercase;padding:12px 22px;letter-spacing:.5px}
.btn.dark{background:var(--ink)}

.services{height:400px;background:var(--band);display:flex;gap:28px;padding:32px 80px}
.service{flex:1;height:336px;display:flex;position:relative;overflow:hidden;background:linear-gradient(135deg,var(--gold-light),var(--gold-dark))}
.service .copy{width:52%;padding:30px 24px;color:#fff}
.service h3{font-size:17px;text-transform:uppercase;margin-bottom:8px}
.service p{font-size:12px;font-weight:600;text-transform:uppercase;margin-bottom:20px}
.service .photo{flex:1}
.photo-truck{background:linear-gradient(160deg,#d8c9a3,#a58b52 55%,#6b5a35)}
.photo-coins{background:linear-gradient(160deg,#e8e2d2,#b59654 55%,#7a6334)}

.welcome{height:420px;background:var(--grey);display:flex;align-items:center;padding:0 80px}
.welcome .name{width:440px;font-family:"Montserrat",sans-serif;font-weight:700;font-size:64px;line-height:1.05;color:var(--gold)}
.welcome .about{margin-left:72px;width:528px}
.welcome h2{font-size:26px;font-weight:600;color:var(--ink);text-transform:uppercase}
.rule{width:60px;height:3px;background:var(--gold);margin:12px 0 18px}
.welcome p{font-size:13px;line-height:22px;margin-bottom:26px}

.news{height:700px;padding-top:52px;text-align:center}
.news h2{font-size:28px;font-weight:600;color:var(--ink);text-transform:uppercase}
.news .rule{margin:12px auto 14px}
.news .lead{font-size:12px;color:var(--muted)}
.cards{display:flex;gap:32px;padding:28px 80px 0}
.card{flex:1;height:520px;background:#fff;box-shadow:0 2px 10px rgba(0,0,0,.12);position:relative}
.card .photo{height:220px}
.n1{background:linear-gradient(160deg,#1f2c58,#c5763c 60%,#3d2a1c)}
.n2{background:linear-gradient(160deg,#3a1c1c,#c1452f 55%,#6b2a22)}
.n3{background:linear-gradient(160deg,#b8b3a6,#8f7a52 55%,#4c4130)}
.card .date{font-size:12px;color:var(--muted);margin:26px 0 8px}
.card h3{font-size:13px;font-weight:700;color:var(--ink);text-transform:uppercase;padding:0 40px;line-height:20px}
.card p{font-size:12px;line-height:20px;color:var(--muted);padding:16px 36px 0}
.card .go{position:absolute;left:50%;bottom:28px;transform:translateX(-50%);width:56px;height:56px;border-radius:50%;background:var(--ink);display:flex;align-items:center;justify-content:center}
.card .go.gold{background:var(--gold)}

.testimonial{height:280px;background:var(--gold);display:flex;align-items:center;padding:0 120px 0 164px;color:#fff;position:relative}
.testimonial blockquote{width:640px;font-size:13px;line-height:22px;position:relative}
.testimonial blockquote::before{content:"\201C";position:absolute;left:-36px;top:-16px;font-size:48px;font-family:Georgia,serif}
.testimonial .who{margin-top:18px;font-family:"Montserrat",sans-serif;font-size:12px;font-weight:700;text-transform:uppercase}
.testimonial .role{font-size:11px;font-weight:400;text-transform:none}
.portrait{margin-left:auto;width:180px;height:180px;border-radius:50%;border:5px solid #fff;background:linear-gradient(160deg,#e9d8c4,#9a6a4a 60%,#4a3020)}
.t-arrow{position:absolute;top:126px;font-size:26px;color:rgba(255,255,255,.7)}

.footer{height:272px;background:var(--charcoal);color:#ccc;position:relative}
.footer .cols{display:flex;padding:40px 80px 0}
.footer .brand{width:420px;font-size:24px;margin-top:30px}
.footer h3{font-size:13px;color:#fff;text-transform:uppercase;margin-bottom:18px}
.links{width:300px}
.links ul{list-style:none;columns:2;font-size:12px;line-height:26px}
.news-sign{flex:1}
.news-sign p{font-size:12px;margin-bottom:16px}
.field{display:flex;width:300px;height:36px}
.field span{flex:1;background:#fff;color:#999;font-size:12px;line-height:36px;padding-left:12px}
.field i{width:40px;background:var(--gold);display:flex;align-items:center;justify-content:center}
.copyright{position:absolute;left:0;right:0;bottom:0;height:48px;line-height:48px;text-align:center;font-size:11px;border-top:1px solid #3b3a38;color:#aaa}
</style>
</head>
<body>
<header class="top">
  <div class="brand"><span class="mark"></span>Halverstone Minerals</div>
  <div class="call">
    <span class="ico"><svg width="18" height="18" viewBox="0 0 24 24"><path fill="#fff" d="M6.6 10.8a15.1 15.1 0 006.6 6.6l2.2-2.2c.3-.3.7-.4 1-.2 1.1.4 2.3.6 3.6.6.6 0 1 .4 1 1V20c0 .6-.4 1-1 1A17 17 0 013 4c0-.6.4-1 1-1h3.5c.6 0 1 .4 1 1 0 1.3.2 2.5.6 3.6.1.3 0 .7-.2 1z"/></svg></span>
    CALL US : (000) 000 000
  </div>
</header>
<nav class="nav">
  <a>Home</a><a>Who We Are</a><a>What We Do</a><a>Corporate Mission</a><a>Vision &amp; Strategy</a><a>Contact Us</a>
</nav>

<section class="hero" role="img" aria-label="Photo of an underground mine tunnel lit by warm lamps">
  <span class="arrow left"><svg width="12" height="12" viewBox="0 0 12 12"><path d="M8 1L3 6l5 5" stroke="#333" stroke-width="2" fill="none"/></svg></span>
  <h1>HALVERSTONE MINERALS</h1>
  <p>Sed ut perspiciatis unde omnis iste natus error sit voluptatem accusantium dolo remque laudantium, totam rem aperiam, eaque ipsa quae</p>
  <span class="btn">Click here for more info</span>
  <span class="arrow right"><svg width="12" height="12" viewBox="0 0 12 12"><path d="M4 1l5 5-5 5" stroke="#333" stroke-width="2" fill="none"/></svg></span>
</section>

<section class="services">
  <article class="service">
    <div class="copy"><h3>International Mining</h3><p>Sed ut perspiciatis unde omnis</p><span class="btn dark">Read More</span></div>
    <div class="photo photo-truck" role="img" aria-label="Photo of a large mining haul truck"></div>
  </article>
  <article class="service">
    <div class="copy"><h3>Private Investment</h3><p>Sed ut perspiciatis unde omnis</p><span class="btn dark">Read More</span></div>
    <div class="photo photo-coins" role="img" aria-label="Photo of rising stacks of coins"></div>
  </article>
</section>

<section class="welcome">
  <div class="name">Halverstone Minerals</div>
  <div class="about">
    <h2>Welcome to our company</h2>
    <div class="rule"></div>
    <p>We are a global mining and private investment group with long experience across many commodities. From our base in Dubai we build projects in Africa, Central and South America, working with partners, funds and exchanges to bring resources to market with care, rigour and lasting value for every investor.</p>
    <span class="btn">Read More</span>
  </div>
</section>

<section class="news">
  <h2>Latest News</h2>
  <div class="rule"></div>
  <p class="lead">Read the latest updates from our projects, partners and markets across the regions where we operate and invest.</p>
  <div class="cards">
    <article class="card">
      <div class="photo n1" role="img" aria-label="Photo of a mining site at night under floodlights"></div>
      <p class="date">Posted 02 Jun, 2016</p>
      <h3>Sed ut perspiciatis unde omnis iste natus error sit</h3>
      <p>New site studies confirm strong grades and open the way for the next stage of work with our partners.</p>
      <span class="go"><svg width="12" height="12" viewBox="0 0 12 12"><path d="M4 1l5 5-5 5" stroke="#fff" stroke-width="2" fill="none"/></svg></span>
    </article>
    <article class="card">
      <div class="photo n2" role="img" aria-label="Photo of molten metal being poured in a foundry"></div>
      <p class="date">Posted 02 Jun, 2016</p>
      <h3>Sed ut perspiciatis unde omnis iste natus error sit</h3>
      <p>New site studies confirm strong grades and open the way for the next stage of work with our partners.</p>
      <span class="go gold"><svg width="12" height="12" viewBox="0 0 12 12"><path d="M4 1l5 5-5 5" stroke="#fff" stroke-width="2" fill="none"/></svg></span>
    </article>
    <article class="card">
      <div class="photo n3" role="img" aria-label="Photo of excavators working in an open pit"></div>
      <p class="date">Posted 02 Jun, 2016</p>
      <h3>Sed ut perspiciatis unde omnis iste natus error sit</h3>
      <p>New site studies confirm strong grades and open the way for the next stage of work with our partners.</p>
      <span class="go"><svg width="12" height="12" viewBox="0 0 12 12"><path d="M4 1l5 5-5 5" stroke="#fff" stroke-width="2" fill="none"/></svg></span>
    </article>
  </div>
</section>

<section class="testimonial">
  <span class="t-arrow" style="left:44px">&#8249;</span>
  <div>
    <blockquote>Working with this team has been clear and steady from the first call. They know the ground, the markets and the people, and they carry every project through with real care and sound judgement.</blockquote>
    <p class="who">Dana Ellory<br><span class="role">Investor, Cape Town</span></p>
  </div>
  <div class="portrait" role="img" aria-label="Portrait photo of the client giving the testimonial"></div>
  <span class="t-arrow" style="right:44px">&#8250;</span>
</section>

<footer class="footer">
  <div class="cols">
    <div class="brand"><span class="mark"></span>Halverstone Minerals</div>
    <div class="links">
      <h3>Quick Links</h3>
      <ul><li>Home</li><li>Who we are</li><li>What we do</li><li>Corporate Mission</li><li>Vision &amp; Strategy</li><li>Contact Us</li></ul>
    </div>
    <div class="news-sign">
      <h3>Newsletter</h3>
      <p>Sign up for news and project updates sent to your inbox.</p>
      <div class="field"><span>Enter Your Email Id</span><i><svg width="14" height="14" viewBox="0 0 24 24"><path fill="#fff" d="M2 21l21-9L2 3v7l15 2-15 2z"/></svg></i></div>
    </div>
  </div>
  <div class="copyright">&copy; Copy Right 2016 Halverstone Minerals All rights reserved</div>
</footer>
</body>
</html>
```